Professional & attention grabbing.

A business card design, front and back. I already have a logo I will attach, but I am open to something new as well.
Things to include:
Name:
Title:
Phone:
Email:
Wanting something that is professional but attention grabbing.
Also we do a lot of work using drones on natural gas pipelines (leading the future)if you want to include any of that. I'm open to ideas.
Target Market(s)
Natural gas transmission industry / greenhouse gas mitigation industry
Industry/Entity Type
Business
Colors
Designer to choose colors to be used in the design.
Look and feel
Each slider illustrates characteristics of the customer's brand and the style your logo design should communicate.

```html
<!DOCTYPE html>
<html lang="en">
<head>
<meta charset="utf-8">
<title>Veyla Inspections — Business Card</title>
<link rel="stylesheet" href="https://fonts.googleapis.com/css2?family=Krona+One&family=Roboto:wght@400;700&display=swap">
<style>
  :root {
    --page-bg: #e9e6e2;
    --card-bg: #f7f7f6;
    --card-edge: #dcdcdc;
    --brand-red: #b3262b;
    --accent-wash: rgba(179, 38, 43, 0.09);
    --accent-wash-edge: rgba(179, 38, 43, 0.04);
    --ink-dark: #2e2e30;
    --ink-body: #3a3a3c;
  }
  * { box-sizing: border-box; margin: 0; padding: 0; }
  html, body {
    width: 1200px;
    height: 1010px;
    overflow: hidden;
    background: var(--page-bg);
  }
  .canvas {
    width: 1200px;
    height: 1010px;
    display: flex;
    align-items: center;
    justify-content: center;
  }
  .business-card {
    position: relative;
    width: 1000px;
    height: 578px;
    overflow: hidden;
    background: var(--card-bg);
    border: 1px solid var(--card-edge);
    box-shadow: 0 10px 30px rgba(0, 0, 0, 0.12);
    font-family: "Roboto", Arial, sans-serif;
    color: var(--ink-body);
  }
  .accent-disc {
    position: absolute;
    left: 520px;
    top: 20px;
    width: 620px;
    height: 620px;
    border-radius: 50%;
    background: radial-gradient(circle at 40% 40%, var(--accent-wash), var(--accent-wash-edge));
  }
  .brand {
    position: absolute;
    left: 43px;
    top: 104px;
    display: flex;
    align-items: center;
    gap: 18px;
  }
  .brand-mark {
    width: 48px;
    height: 48px;
    background: var(--brand-red);
  }
  .brand-name {
    font-weight: 700;
    font-size: 50px;
    line-height: 1;
    color: var(--ink-dark);
  }
  .person {
    position: absolute;
    left: 43px;
    top: 340px;
  }
  .person-name {
    font-family: "Krona One", "Roboto", sans-serif;
    font-weight: 400;
    font-size: 29px;
    color: var(--brand-red);
    letter-spacing: 1px;
    line-height: 1.1;
  }
  .person-title {
    margin-top: 10px;
    font-size: 21px;
    color: var(--ink-body);
  }
  .contact-list {
    position: absolute;
    left: 43px;
    top: 447px;
    list-style: none;
  }
  .contact-item {
    display: flex;
    align-items: center;
    gap: 18px;
    height: 33px;
    font-size: 22px;
    color: var(--ink-body);
  }
  .contact-icon {
    width: 22px;
    height: 22px;
    flex: none;
  }
</style>
</head>
<body>
<main class="canvas">
  <article class="business-card">
    <div class="accent-disc" aria-hidden="true"></div>

    <header class="brand">
      <span class="brand-mark" aria-hidden="true"></span>
      <span class="brand-name">Veyla Inspections</span>
    </header>

    <section class="person">
      <h1 class="person-name">MARA HOLT</h1>
      <p class="person-title">Managing Director</p>
    </section>

    <ul class="contact-list">
      <li class="contact-item">
        <svg class="contact-icon" viewBox="0 0 24 24" aria-hidden="true">
          <path fill="var(--brand-red)" d="M3 8c0-2 3-4 9-4s9 2 9 4v2h-5V8c-1-.6-2.5-1-4-1s-3 .4-4 1v2H3zM6 12h12l2 8H4z"/>
          <circle cx="12" cy="16" r="2" fill="var(--card-bg)"/>
        </svg>
        <span>1300 555 018</span>
      </li>
      <li class="contact-item">
        <svg class="contact-icon" viewBox="0 0 24 24" aria-hidden="true">
          <g fill="none" stroke="var(--brand-red)" stroke-width="2">
            <circle cx="12" cy="12" r="9"/>
            <ellipse cx="12" cy="12" rx="4" ry="9"/>
            <line x1="3" y1="12" x2="21" y2="12"/>
          </g>
        </svg>
        <span>www.veylainspections.com</span>
      </li>
      <li class="contact-item">
        <svg class="contact-icon" viewBox="0 0 24 24" aria-hidden="true">
          <rect x="2" y="5" width="20" height="14" fill="var(--brand-red)"/>
          <path d="M2 5l10 8 10-8" fill="none" stroke="var(--card-bg)" stroke-width="1.6"/>
        </svg>
        <span>mara.holt@veylainspections.com</span>
      </li>
    </ul>
  </article>
</main>
</body>
</html>
```